Stonebridge Building and Projects business cards

A business card with watermark background (construction work)

Company logo attached

Home improvement projects
House renovations
Bathroom and kitchen renovations
House extensions
New builds and granny flats

Director Omar Haddani
(Phone number)
omar@sbpbuilding.com.au
(Instagram logo) sbp_building

```html
<!DOCTYPE html>
<html lang="en">
<head>
<meta charset="utf-8">
<title>Stonebridge Building and Projects – Business Cards</title>
<link href="https://fonts.googleapis.com/css2?family=Roboto:wght@400;500&family=Signika:wght@600&family=Rokkitt:wght@400&display=swap" rel="stylesheet">
<style>
  :root {
    --bg: #2a2a2a;
    --card: #f8f8f8;
    --blue: #0a76bd;
    --ink: #2e2e2e;
    --muted: #bfbfbf;
  }
  * { box-sizing: border-box; margin: 0; padding: 0; }
  html, body { width: 1138px; height: 1200px; overflow: hidden; }
  body { background: var(--bg); font-family: "Roboto", sans-serif; color: var(--ink); position: relative; }

  .card {
    position: absolute; top: 288px; height: 622px;
    background: var(--card); border-radius: 16px; overflow: hidden;
    text-align: center;
  }
  .card--front { left: 166px; width: 376px; }
  .card--back  { left: 604px; top: 290px; height: 620px; width: 373px; }

  .brand { position: absolute; left: 0; right: 0; }
  .card--front .brand { top: 150px; }
  .card--back .brand { top: 100px; }
  .brand__name {
    font-family: "Roboto", sans-serif; font-weight: 500; color: var(--blue);
    font-size: 31px; line-height: 1.15;
  }
  .card--back .brand__name { font-size: 29px; }
  .tagline {
    display: inline-block; margin-top: 12px; padding: 0 4px 3px;
    font-family: "Rokkitt", serif; font-size: 22px; color: var(--blue);
    border-bottom: 1.5px solid var(--blue);
  }
  .card--back .tagline { font-size: 20px; margin-top: 10px; }

  .services { position: absolute; top: 365px; left: 0; right: 0; list-style: none; font-size: 16.5px; }
  .services li { height: 32px; display: flex; justify-content: center; }
  .services li span { display: inline-block; padding: 5px 14px 5px; border-bottom: 1.5px solid var(--blue); height: 32px; }
  .services li.plain span { border-bottom: none; }
  .services .sep { color: var(--blue); margin: 0 8px; }

  .social { position: absolute; left: 0; right: 0; font-size: 16.5px; display: flex; justify-content: center; align-items: center; gap: 10px; }
  .card--front .social { top: 518px; }
  .card--back .social { top: 539px; }
  .social__mark { width: 15px; height: 15px; border: 2px solid var(--blue); border-radius: 4px; }

  .site-band {
    position: absolute; left: 0; right: 0; bottom: 0; height: 47px;
    background: var(--blue); color: #fff; font-size: 16.5px;
    display: flex; align-items: center; justify-content: center;
  }

  .person { position: absolute; top: 330px; left: 0; right: 0; }
  .person__name { font-family: "Signika", sans-serif; font-weight: 600; font-size: 26px; color: var(--blue); }
  .person__role { font-size: 16.5px; margin-top: 2px; }

  .contact-icons { position: absolute; top: 406px; left: 0; right: 0; display: flex; justify-content: center; align-items: center; }
  .rule { width: 48px; height: 2px; background: var(--ink); margin: 0 16px; }

  .contact { position: absolute; top: 448px; left: 0; right: 0; list-style: none; font-size: 16.5px; line-height: 24.5px; }
  .contact .hl { color: var(--blue); }
</style>
</head>
<body>

<section class="card card--front">
  <div class="brand">
    <div class="brand__name">Stonebridge<br>Building and Projects</div>
    <div class="tagline">Solid from the ground up</div>
  </div>

  <ul class="services">
    <li><span>Home Improvement Projects</span></li>
    <li><span>Bathroom &amp; Kitchen Renovations</span></li>
    <li><span>New Builds &amp; Granny Flats</span></li>
    <li class="plain"><span>House Renovations<b class="sep">|</b>House Extensions</span></li>
  </ul>

  <div class="social"><span class="social__mark"></span>sbp_building</div>
  <div class="site-band">www.sbpbuilding.com.au</div>
</section>

<section class="card card--back">
  <div class="brand">
    <div class="brand__name">Stonebridge<br>Building and Projects</div>
    <div class="tagline">Solid from the ground up</div>
  </div>

  <div class="person">
    <div class="person__name">Omar Haddani</div>
    <div class="person__role">Managing Director</div>
  </div>

  <div class="contact-icons">
    <span class="rule"></span>
    <svg width="86" height="28" viewBox="0 0 86 28" aria-hidden="true">
      <g fill="none" stroke="#0a76bd" stroke-width="1.6">
        <circle cx="14" cy="14" r="12"/><circle cx="43" cy="14" r="12"/><circle cx="72" cy="14" r="12"/>
      </g>
      <g fill="#0a76bd">
        <path d="M8 12c0-2 2-4 6-4s6 2 6 4l-2 1-1-2h-6l-1 2zM9 14h10v5H9z"/>
        <rect x="36" y="9" width="14" height="10" rx="1"/>
        <circle cx="72" cy="14" r="6.5"/>
      </g>
      <g fill="none" stroke="#fff" stroke-width="1.2">
        <path d="M36.5 9.5l6.5 5.5 6.5-5.5"/>
        <path d="M65.5 14h13M72 7.5v13M72 7.5c-3.5 3-3.5 10 0 13M72 7.5c3.5 3 3.5 10 0 13"/>
      </g>
    </svg>
    <span class="rule"></span>
  </div>

  <ul class="contact">
    <li>0400 318 672</li>
    <li>omar@sbpbuilding.com.au</li>
    <li>www.<span class="hl">sbpbuilding</span>.com.au</li>
  </ul>

  <div class="social"><span class="social__mark"></span>sbp_building</div>
</section>

</body>
</html>
```